Business card design needed

Need a new business card design for a new business in Sydney, Australia called 'Brovane Australia'. The business deals in consulting for new sales, sales leadership and customer service consultancy. Want the business card to look professional and clean

Industry/Entity Type

Leadership

Contact Information for Business Card

Brovane Australia
Conrad Pilling
Managing Director

14 Mardock Lane
Harwin Vale NSW 2187

0493 715 062
conrad@brovane.com.au
www.brovane.com.au

```html
<!DOCTYPE html>
<html lang="en">
<head>
<meta charset="utf-8">
<title>Brovane Australia – Business Card</title>
<link rel="stylesheet" href="https://fonts.googleapis.com/css2?family=Arimo:wght@400;700&display=swap">
<style>
  :root {
    --page-bg: #ffffff;
    --card-bg: #0c0c0c;
    --text-light: #f4f4f4;
    --accent-red: #e8401c;
    --accent-blue: #13329a;
    --accent-white: #f7f7f7;
    --brand-grey: #7e8789;
    --shade-navy: #121a33;
    --shade-grey: #262626;
    --shade-brown: #231c1a;
  }
  html, body {
    margin: 0;
    padding: 0;
    width: 1200px;
    height: 741px;
    overflow: hidden;
    background: var(--page-bg);
  }
  .canvas {
    position: relative;
    width: 1200px;
    height: 741px;
  }
  .business-card {
    position: absolute;
    left: 120px;
    top: 75px;
    width: 960px;
    height: 592px;
    background: var(--card-bg);
    font-family: "Arimo", Arial, sans-serif;
    color: var(--text-light);
    overflow: hidden;
  }
  .illustration {
    position: absolute;
    border-radius: 40px 60px 60px 40px;
  }
  .illustration--shade-navy {
    left: -20px; top: 240px; width: 560px; height: 380px;
    background: radial-gradient(ellipse at 40% 40%, #16203f 0%, var(--shade-navy) 70%);
    border-radius: 120px 160px 60px 40px;
  }
  .illustration--shade-grey {
    left: 190px; top: 12px; width: 210px; height: 140px;
    background: var(--shade-grey);
  }
  .illustration--shade-brown {
    left: 590px; top: 62px; width: 350px; height: 270px;
    background: var(--shade-brown);
    border-radius: 60px 140px 120px 60px;
  }
  .illustration--white {
    left: 433px; top: 113px; width: 118px; height: 87px;
    background: var(--accent-white);
  }
  .illustration--red {
    left: 525px; top: 273px; width: 181px; height: 131px;
    background: var(--accent-red);
  }
  .illustration--blue {
    left: 250px; top: 285px; width: 241px; height: 178px;
    background: var(--accent-blue);
  }
  .website {
    position: absolute;
    left: 18px;
    top: 32px;
    font-size: 20px;
    letter-spacing: 0.5px;
  }
  .contact-person {
    position: absolute;
    right: 39px;
    top: 22px;
    text-align: right;
  }
  .person-name {
    font-size: 25px;
    letter-spacing: 3px;
    line-height: 32px;
  }
  .person-title {
    font-size: 25px;
    letter-spacing: 2.5px;
    line-height: 32px;
    color: var(--accent-red);
  }
  .brand {
    position: absolute;
    left: 262px;
    top: 208px;
    display: flex;
    align-items: center;
    gap: 14px;
  }
  .brand-mark {
    width: 22px;
    height: 22px;
    background: var(--accent-red);
  }
  .brand-name {
    font-size: 54px;
    font-weight: 700;
    color: var(--brand-grey);
    letter-spacing: -0.5px;
    line-height: 1;
  }
  .address-line {
    position: absolute;
    left: 0;
    right: 0;
    top: 526px;
    text-align: center;
    font-size: 21px;
    letter-spacing: 0.3px;
  }
</style>
</head>
<body>
  <main class="canvas">
    <section class="business-card" aria-label="Brovane Australia business card">
      <div class="illustration illustration--shade-navy" role="img" aria-label="Large faint navy hand-shaped bird illustration"></div>
      <div class="illustration illustration--shade-grey" role="img" aria-label="Faint grey hand-shaped bird illustration"></div>
      <div class="illustration illustration--shade-brown" role="img" aria-label="Faint dark brown hand-shaped bird illustration"></div>
      <div class="illustration illustration--white" role="img" aria-label="White hand-shaped bird illustration"></div>
      <div class="illustration illustration--red" role="img" aria-label="Red hand-shaped bird illustration"></div>
      <div class="illustration illustration--blue" role="img" aria-label="Blue hand-shaped bird illustration"></div>

      <div class="website">www.brovane.com.au</div>

      <div class="contact-person">
        <div class="person-name">Conrad Pilling</div>
        <div class="person-title">Managing Director</div>
      </div>

      <div class="brand">
        <span class="brand-mark" aria-hidden="true"></span>
        <span class="brand-name">Brovane Australia</span>
      </div>

      <div class="address-line">14 Mardock Lane Harwin Vale NSW 2187 0493 715 062 conrad@brovane.com.au</div>
    </section>
  </main>
</body>
</html>
```